We are a recruitment company based in Norwich/Cambridge England.
I have included our company logo which we want to remain the same.

What we are looking for is a new creative Business card which will really stand out!!

Contact Information for Business Card

Harriet Dunmore
email: Harriet@plavex.co.uk
Address: Brackwell House
Fenmoor Enterprise Park
Partridge Way
Norwich
QB9 3KX
Tel:01632 960418

```html
<!DOCTYPE html>
<html lang="en">
<head>
<meta charset="utf-8">
<title>Plavex Business Card</title>
<link rel="stylesheet" href="https://fonts.googleapis.com/css2?family=Open+Sans:wght@400;600;700&display=swap">
<style>
  :root {
    --lime: #9fcc1c;
    --grey: #8d8a90;
    --ink: #4a4a4a;
    --paper: #ffffff;
    --backdrop: #2b2b2d;
  }
  * { box-sizing: border-box; margin: 0; padding: 0; }
  html, body {
    width: 1200px; height: 900px; overflow: hidden;
    background: var(--backdrop);
    font-family: "Open Sans", Arial, sans-serif;
  }
  .canvas { position: relative; width: 1200px; height: 900px; }
  .card {
    position: absolute; width: 520px; height: 310px;
    background: var(--paper); border-radius: 18px; overflow: hidden;
    box-shadow: 0 14px 30px rgba(0,0,0,0.45);
  }
  .card--front { left: 70px; top: 130px; }
  .card--back { left: 610px; top: 460px; }
  .card__sweep { position: absolute; inset: 0; width: 100%; height: 100%; }
  .brand { position: absolute; display: flex; align-items: center; gap: 14px; }
  .brand__dot { border-radius: 50%; background: var(--lime); }
  .brand__name { color: var(--grey); font-weight: 700; letter-spacing: -0.5px; line-height: 1; }
  .card--front .brand { left: 38px; top: 92px; }
  .card--front .brand__dot { width: 42px; height: 42px; }
  .card--front .brand__name { font-size: 42px; }
  .card--back .brand { left: 50%; top: 50%; transform: translate(-50%, -50%); }
  .card--back .brand__dot { width: 62px; height: 62px; }
  .card--back .brand__name { font-size: 62px; }
  .person { position: absolute; left: 40px; top: 170px; }
  .person__name { color: var(--lime); font-weight: 700; font-size: 18px; line-height: 1.2; }
  .person__role { color: var(--ink); font-size: 15px; line-height: 1.3; }
  .contact {
    position: absolute; right: 16px; top: 20px; text-align: right;
    color: var(--paper); font-size: 12px; font-style: normal; line-height: 1.4;
  }
  .contact__line { display: flex; justify-content: flex-end; align-items: center; gap: 6px; }
  .contact__icon { width: 11px; height: 11px; flex: none; }
  .contact__address { margin-top: 8px; }
</style>
</head>
<body>
<main class="canvas">
  <section class="card card--front">
    <svg class="card__sweep" viewBox="0 0 520 310" preserveAspectRatio="none" aria-hidden="true">
      <path d="M320 0 L520 0 L520 310 L0 310 L0 290 C250 285 320 200 320 0 Z" fill="var(--lime)"/>
      <path d="M0 264 C240 258 306 186 312 10 C314 196 246 280 0 282 Z" fill="var(--grey)"/>
    </svg>

    <div class="brand">
      <span class="brand__dot"></span>
      <span class="brand__name">Plavex</span>
    </div>

    <div class="person">
      <p class="person__name">Harriet Dunmore</p>
      <p class="person__role">President</p>
    </div>

    <address class="contact">
      <p class="contact__line">01632 960418
        <svg class="contact__icon" viewBox="0 0 12 12"><path d="M3 1 L5 3.5 L4 5 C5 7 6 8 7.5 8.5 L9 7.5 L11 9.5 L9.5 11 C5 10.5 1.5 7 1 2.5 Z" fill="currentColor"/></svg>
      </p>
      <p class="contact__line">Harriet@plavex.co.uk
        <svg class="contact__icon" viewBox="0 0 12 12"><rect x="0.5" y="2.5" width="11" height="7" fill="none" stroke="currentColor"/><path d="M0.5 2.5 L6 7 L11.5 2.5" fill="none" stroke="currentColor"/></svg>
      </p>
      <p class="contact__line">www.plavex.co.uk
        <svg class="contact__icon" viewBox="0 0 12 12"><circle cx="6" cy="6" r="5.2" fill="none" stroke="currentColor"/><ellipse cx="6" cy="6" rx="2.3" ry="5.2" fill="none" stroke="currentColor"/><path d="M1 6 H11" stroke="currentColor"/></svg>
      </p>
      <div class="contact__address">
        <p>Brackwell House</p>
        <p>Fenmoor Enterprise Park</p>
        <p>Partridge Way Norwich QB9 3KX</p>
      </div>
    </address>
  </section>

  <section class="card card--back">
    <div class="brand">
      <span class="brand__dot"></span>
      <span class="brand__name">Plavex</span>
    </div>
  </section>
</main>
</body>
</html>
```